Business Card Design for Marketing Firm

Looking for business card design for higher end marketing firm. Clean but impressionable/trendy. We are a marketing firm that represents manufacturers in the foodservice equipment and supply industry. Our customers are end users such has hotels, restaurants, country clubs, convention centers and casinos as well as distributors of restaurants supplies and equipment, and manufacturers of foodservice equipment and supplies.
Target Market(s)
Hotels, Restaurants, Supply & Equipment Distributors, Foodservice Manufacturers
Industry/Entity Type
Foodservice/Hospitality
Contact Information for Business Card
Name, Title, Contact Number, Email, Website, Social Media, Address
Requirements
Must have
- Clean & Simple but Serious and Impressionable

```html
<!DOCTYPE html>
<html lang="en">
<head>
<meta charset="utf-8">
<title>Harbor Table Reps — Business Cards</title>
<link rel="stylesheet" href="https://fonts.googleapis.com/css2?family=Lato:wght@400;700;900&display=swap">
<style>
  :root {
    --navy: #07077f;
    --paper: #ffffff;
    --ink-grey: #5a5a5a;
    --rule-grey: #8a8a8a;
    --backdrop-top: #5c5e61;
    --backdrop-bottom: #2a2b2d;
  }
  * { margin: 0; padding: 0; box-sizing: border-box; }
  html, body { width: 1200px; height: 952px; overflow: hidden; }
  body {
    background: linear-gradient(160deg, var(--backdrop-top), var(--backdrop-bottom));
    font-family: "Lato", sans-serif;
    position: relative;
  }
  .card {
    position: absolute;
    top: 327px;
    width: 520px;
    height: 298px;
    border-radius: 22px;
    overflow: hidden;
    box-shadow: 0 10px 26px rgba(0,0,0,0.35);
  }
  .card--front { left: 50px; background: var(--paper); }
  .card--back { left: 630px; background: var(--navy); }

  .identity { position: absolute; left: 40px; top: 38px; }
  .identity__name {
    color: var(--navy);
    font-weight: 900;
    font-size: 25px;
    letter-spacing: 0.5px;
    line-height: 1;
  }
  .identity__title {
    color: var(--ink-grey);
    font-size: 17px;
    margin-top: 6px;
  }
  .identity__rule {
    width: 46px; height: 2px;
    background: var(--rule-grey);
    margin-top: 10px;
  }

  .contacts { position: absolute; left: 40px; top: 140px; list-style: none; }
  .contacts li {
    display: flex; align-items: flex-start;
    color: var(--ink-grey);
    font-size: 12.5px;
    line-height: 1.25;
    margin-bottom: 7px;
  }
  .contacts .icon {
    width: 15px; height: 15px; flex: none;
    background: var(--navy);
    border-radius: 3px;
    margin-right: 9px;
    display: flex; align-items: center; justify-content: center;
  }
  .contacts .icon svg { width: 10px; height: 10px; }

  .brand-mark {
    position: absolute;
    display: flex; align-items: center; gap: 12px;
    font-weight: 700;
  }
  .brand-mark__dot { border-radius: 50%; flex: none; }

  .card--front .brand-mark { right: 36px; bottom: 40px; color: var(--navy); font-size: 30px; }
  .card--front .brand-mark__dot { width: 22px; height: 22px; background: var(--navy); }

  .card--back .brand-mark {
    left: 50%; top: 50%; transform: translate(-50%, -50%);
    color: var(--paper); font-size: 28px; letter-spacing: 2px; white-space: nowrap;
  }
  .card--back .brand-mark__dot { width: 18px; height: 18px; background: var(--paper); }
</style>
</head>
<body>

<section class="card card--front" aria-label="Business card front">
  <div class="identity">
    <p class="identity__name">DANIEL R. WHITMORE</p>
    <p class="identity__title">Managing Director</p>
    <div class="identity__rule"></div>
  </div>

  <ul class="contacts">
    <li>
      <span class="icon"><svg viewBox="0 0 10 10"><circle cx="5" cy="4" r="3" fill="none" stroke="#fff" stroke-width="1.4"/><path d="M5 7 L5 10" stroke="#fff" stroke-width="1.4"/></svg></span>
      <span>1720 Linden Park Avenue<br>Springfield, IL 62704</span>
    </li>
    <li>
      <span class="icon"><svg viewBox="0 0 10 10"><path d="M2 1 L4 1 L4.6 3.4 L3.4 4.4 Q4.6 6.2 5.8 6.8 L6.8 5.6 L9 6.2 L9 8.2 Q5 9 2 5.5 Q1 3 2 1 Z" fill="#fff"/></svg></span>
      <span>+00 555 018 42</span>
    </li>
    <li>
      <span class="icon"><svg viewBox="0 0 10 10"><rect x="1" y="2.2" width="8" height="5.6" fill="none" stroke="#fff" stroke-width="1.1"/><path d="M1 2.2 L5 5.6 L9 2.2" fill="none" stroke="#fff" stroke-width="1.1"/></svg></span>
      <span>hello@harbortable.com</span>
    </li>
    <li>
      <span class="icon"><svg viewBox="0 0 10 10"><circle cx="5" cy="5" r="3.8" fill="none" stroke="#fff" stroke-width="1.1"/><path d="M1.2 5 H8.8 M5 1.2 Q2.8 5 5 8.8 M5 1.2 Q7.2 5 5 8.8" fill="none" stroke="#fff" stroke-width="0.9"/></svg></span>
      <span>www.harbortable.com</span>
    </li>
  </ul>

  <div class="brand-mark">
    <span class="brand-mark__dot"></span>
    <span>Harbor Table Reps</span>
  </div>
</section>

<section class="card card--back" aria-label="Business card back">
  <div class="brand-mark">
    <span class="brand-mark__dot"></span>
    <span>HARBOR TABLE REPS</span>
  </div>
</section>

</body>
</html>
```